Reach Crafters Unique Marketing Website Design

I am starting a new company that is a thought leader in the marketing consulting space. The company is called Reach Crafters. We intend to build a Wordpress site on the Astra Theme with the Spectra builder. Our goal is to become the leading voice that empowers high-ticket service business leaders to become Reach Crafters by equipping them with the cutting-edge frameworks and decision grade intelligence taught in leading business schools. What we are looking for is a website design that is clean and professional, making some use of white space well also being eye catching and distinctive in the consulting space. We will probably want to have a video on the homepage not in the hero section, but just below to explain the company and what we do. Our tagline is "Be found. Be chosen." I have attached a brand guide with some messaging, our typography choices, and our color system. The full site will have a primary nav that is four pages - About us, Services, Insights (essentially a blog), and Contact Us. The goal of this project is to develop an art direction that I can give to a designer to build loads of new pages.

Target Market(s)

Business owners (mostly male) from 30-60 years old, looking to fix their sales and marketing funnel.

Industry/Entity Type

Marketing consulting

Font styles to use
Sans Serif

Requirements
Must have
• A clean, professional design that builds trust with owners of high-ticket service businesses. We need a space for explainer video, and sections that tell prospects what we do. Would also like to have a blog carousel.
Nice to have
• Social feeds, if possible. See attached documents for colors and fonts.
Should not have
• Our feel is professional enough to be trustworthy, but unique enough to be memorable. Cartoon ideas do not meet the professional test, and we do not want the website to appear feminine.

```html
<!DOCTYPE html>
<html lang="en">
<head>
<meta charset="utf-8">
<title>Reach Crafters</title>
<link href="https://fonts.googleapis.com/css2?family=Oswald:wght@400;500;600&family=Inter:wght@400;500;600;700&family=Libre+Baskerville:wght@700&display=swap" rel="stylesheet">
<style>
:root{
  --blue:#3d5cf5;
  --blue-dark:#2f48d8;
  --navy:#0f1a2c;
  --ink:#1b1f2a;
  --text:#4a4f5c;
  --muted:#6b7080;
  --line:#e3e6ee;
  --soft:#f3f4f8;
  --white:#ffffff;
  --red:#e53935;
  --star:#f5b400;
}
*{box-sizing:border-box;margin:0;padding:0}
html,body{width:1200px;height:5391px;overflow:hidden}
body{position:relative;font-family:"Inter",Arial,sans-serif;color:var(--text);background:var(--white)}
.section{position:absolute;left:0;width:1200px}
.abs{position:absolute}
.heading{font-family:"Oswald","Arial Narrow",sans-serif;font-weight:500;color:var(--ink);text-transform:uppercase;letter-spacing:.2px}
.accent{color:var(--blue);position:relative;display:inline-block}
.accent::after{content:"";position:absolute;left:-2px;right:-4px;bottom:-6px;height:8px;border-bottom:2.5px solid var(--blue);border-radius:0 0 60% 40%/0 0 100% 100%;transform:rotate(-1deg)}
.center-title{left:0;width:1200px;text-align:center;font-size:36px}
.center-sub{left:50%;transform:translateX(-50%);text-align:center;font-size:12.5px;line-height:21px;color:var(--text)}
.btn{display:inline-flex;align-items:center;gap:8px;background:var(--blue);color:#fff;font-size:13px;font-weight:600;text-transform:uppercase;letter-spacing:.3px;justify-content:center}
.btn svg{width:13px;height:13px}

/* nav */
.nav{top:0;height:78px;background:#fff;z-index:5}
.logo{font-family:"Inter",sans-serif;font-weight:700;font-size:19px;color:var(--navy);letter-spacing:.2px}
.nav .brandmark{left:142px;top:27px}
.nav .links{left:412px;top:30px;display:flex;gap:36px;font-size:12px;font-weight:500;color:var(--ink)}
.nav .links .active{color:var(--blue);border-bottom:1.5px solid var(--blue);padding-bottom:5px}
.nav .cta{left:932px;top:19px;width:126px;height:40px;border:1.5px solid var(--blue);color:var(--blue);font-size:12px;font-weight:500;display:flex;align-items:center;justify-content:center;gap:6px}

/* hero */
.hero{top:78px;height:682px;overflow:hidden}
.hero .bg{position:absolute;inset:0;background:linear-gradient(90deg,#1d2330 0%,#3a3d45 38%,#6e5c4e 62%,#8a8177 100%)}
.hero .shade{position:absolute;inset:0;background:linear-gradient(90deg,rgba(10,14,24,.75) 0%,rgba(10,14,24,.35) 50%,rgba(0,0,0,0) 100%)}
.hero h1{left:156px;top:88px;padding-left:14px;border-left:2px solid #fff;font-family:"Oswald",sans-serif;font-weight:400;font-size:48px;line-height:57px;color:#fff;text-transform:uppercase}
.hero p{left:142px;top:279px;width:410px;color:#fff;font-size:14.5px;font-weight:600;line-height:26px}
.hero .btn{left:142px;top:387px;width:242px;height:42px}
.hero svg.cut{position:absolute;left:0;bottom:0}

/* services */
.services{top:740px;height:606px}
.card{background:#fff;box-shadow:0 4px 18px rgba(20,30,60,.08);text-align:center}
.svc{top:181px;width:281px;height:258px}
.svc.featured{border:1.5px solid var(--blue)}
.svc svg{margin-top:28px;width:68px;height:68px}
.svc h3{font-family:"Libre Baskerville",Georgia,serif;font-size:16px;color:var(--ink);margin-top:14px}
.svc p{font-size:12px;line-height:21px;color:var(--text);margin:12px auto 0;width:245px}

/* video */
.video{top:1346px;height:968px;background:linear-gradient(180deg,var(--soft) 0,var(--soft) 424px,#fff 424px)}
.frame{left:142px;top:195px;width:916px;height:515px;background:#fff;padding:14px;box-shadow:0 6px 24px rgba(20,30,60,.12)}
.frame .screen{position:relative;width:100%;height:100%;background:linear-gradient(120deg,#d9dde2 0%,#8a7763 35%,#3d3a38 55%,#7e8a97 80%,#c9cdd2 100%)}
.play{position:absolute;left:409px;top:108px;width:70px;height:70px;border-radius:50%;background:#fff;display:flex;align-items:center;justify-content:center}
.bar{position:absolute;left:22px;right:22px;top:432px;height:3px;background:rgba(255,255,255,.8)}
.bar span{display:block;width:44%;height:100%;background:var(--red)}
.time{position:absolute;top:448px;color:#fff;font-size:14px;font-weight:500}

/* stats */
.stats{top:2314px;height:279px;background:linear-gradient(180deg,#f1f3f8,#eef0f6)}
.stat{top:92px;width:240px;text-align:center}
.stat .num{font-family:"Oswald",sans-serif;font-weight:500;font-size:58px;line-height:66px;color:var(--ink)}
.stat .num b{color:var(--blue);font-weight:500}
.stat .lbl{font-size:14px;color:var(--ink);margin-top:10px}
.divider{top:76px;height:125px;border-left:1.5px dashed #9aa0ae}

/* about */
.about{top:2593px;height:684px}
.about .copy{left:142px;top:88px;width:452px}
.about h2{font-size:36px;margin-bottom:22px}
.about .lead{font-size:15px;font-weight:600;color:var(--ink);margin-bottom:16px;padding-left:4px}
.about .copy p.body{font-size:12.5px;line-height:21px;margin-bottom:14px}
.about .btn{width:163px;height:43px;margin-top:10px}
.badge{left:727px;top:117px;width:98px;height:92px;background:var(--blue);color:#fff;text-align:center;z-index:2}
.badge b{display:block;font-family:"Oswald",sans-serif;font-size:36px;font-weight:500;line-height:42px;margin-top:8px}
.badge span{font-size:11px;line-height:13px;display:block}
.feature{top:527px;width:230px}
.feature h4{font-size:15px;font-weight:500;color:var(--ink)}
.feature p{font-size:11.5px;line-height:21px;margin-top:10px}

/* blog */
.blog{top:3277px;height:739px;background:var(--soft)}
.post{top:199px;width:282px;height:412px;text-align:left}
.post .img{height:178px}
.post .meta{padding:18px 16px 0}
.post .date{font-size:12px;color:var(--blue)}
.post h3{font-size:13.5px;font-weight:500;line-height:22px;color:var(--ink);margin-top:8px}
.post p{font-size:11.5px;line-height:22px;margin-top:12px}
.post .more{display:flex;align-items:center;gap:8px;font-size:12.5px;color:var(--ink);margin-top:20px}
.arrow{width:26px;height:26px;border-radius:50%;display:flex;align-items:center;justify-content:center}
.arrow.off{background:#c9ccd4}
.arrow.on{background:var(--blue)}
.dots{display:flex;gap:15px;align-items:center}
.dots i{width:8px;height:8px;border-radius:50%;background:#c9ccd4;display:block}
.dots i.on{background:var(--blue)}

/* cta */
.cta-band{top:4016px;height:256px;background:linear-gradient(120deg,#3556f0 0%,#4766fa 50%,#3a5af3 100%)}
.cta-band h2{left:142px;top:66px;font-family:"Oswald",sans-serif;font-weight:500;font-size:36px;line-height:46px;color:#fff;text-transform:uppercase}
.cta-band p{left:142px;top:172px;font-size:13.5px;color:#fff}
.subscribe{left:739px;top:105px;width:319px;height:51px;background:#fff;display:flex}
.subscribe span{flex:1;padding-left:18px;line-height:51px;font-size:13px;color:#555}
.subscribe b{width:51px;background:#111;display:flex;align-items:center;justify-content:center}

/* testimonials */
.testimonials{top:4272px;height:600px}
.review{top:220px;width:282px;height:300px}
.avatar{width:62px;height:62px;border-radius:50%;margin:22px auto 0;background:linear-gradient(160deg,#c9d2e3,#7d8798)}
.review h4{font-size:14px;font-weight:500;color:var(--ink);margin-top:16px}
.review .role{font-size:12px;color:var(--text);margin-top:6px}
.stars{color:var(--star);font-size:16px;letter-spacing:3px;margin-top:6px}
.review p{font-size:11.5px;line-height:22px;width:230px;margin:10px auto 0}

/* footer */
.footer{top:4860px;height:531px;background:var(--navy);color:#fff}
.footer svg.top{position:absolute;left:0;top:0}
.footer .brand{left:142px;top:236px}
.footer .brand .logo{color:#fff}
.footer .brand p{font-size:12.5px;line-height:22px;margin-top:22px;width:230px}
.follow{left:142px;top:370px;display:flex;align-items:center;gap:10px;font-size:12.5px}
.follow i{width:22px;height:22px;border-radius:50%;border:1.5px solid #fff;display:block}
.follow i.fill{background:var(--blue);border-color:var(--blue)}
.fcol h5{font-size:15px;font-weight:500;margin-bottom:20px}
.fcol h5::after{content:"";display:block;width:26px;height:1.5px;background:var(--blue);margin-top:6px}
.fcol li{list-style:none;font-size:12.5px;line-height:28px}
.contact-row{display:flex;gap:14px;font-size:12.5px;line-height:21px;margin-bottom:16px;align-items:flex-start}
.contact-row .ic{flex:none;width:28px;height:28px;border-radius:50%;background:#26324a;display:flex;align-items:center;justify-content:center}
.contact-row .ic.blue{background:var(--blue)}
.copyright{left:0;top:500px;width:1200px;text-align:center;font-size:11px;color:#d6d9e0}
.fline{left:0;top:478px;width:1200px;border-top:1px solid #26324a}
</style>
</head>
<body>

<header class="section nav">
  <div class="abs brandmark"><div class="logo">REACH CRAFTERS</div></div>
  <nav class="abs links">
    <span class="active">ABOUT US</span><span>SERVICES</span><span>INSIGHTS</span><span>CONTACT US</span>
  </nav>
  <div class="abs cta">Get Started
    <svg width="11" height="11" viewBox="0 0 12 12"><path d="M2 10L10 2M4 2h6v6" stroke="currentColor" stroke-width="1.5" fill="none"/></svg>
  </div>
</header>

<section class="section hero">
  <div class="bg" role="img" aria-label="Three smiling business professionals in discussion at a meeting table"></div>
  <div class="shade"></div>
  <h1 class="abs">Empowering High-<br>Ticket Service<br>Business Leaders</h1>
  <p class="abs">Become a Reach Crafter with cutting-edge works frameworks and decision-grade intelligence taught in leading business schools.</p>
  <div class="abs btn">Explore Our Services
    <svg viewBox="0 0 12 12"><path d="M2 10L10 2M4 2h6v6" stroke="#fff" stroke-width="1.5" fill="none"/></svg>
  </div>
  <svg class="cut" width="1200" height="130" viewBox="0 0 1200 130">
    <polygon points="0,130 0,102 70,90 760,20 1200,118 1200,130" fill="#fff"/>
    <polygon points="70,90 760,14 760,28 82,93" fill="#3d5cf5"/>
    <polygon points="760,20 1200,80 1200,118" fill="#eef0f5"/>
  </svg>
</section>

<section class="section services">
  <h2 class="abs heading center-title" style="top:44px">Our Core <span class="accent">Services</span></h2>
  <p class="abs center-sub" style="top:106px;width:680px">We provide specialized consulting services designed to transform your marketing and sales funnel into a high-performance demand generation system.</p>

  <div class="abs card svc" style="left:142px">
    <svg viewBox="0 0 68 68" fill="none" stroke="#2a9d8f" stroke-width="2"><rect x="8" y="10" width="52" height="34" rx="2" stroke="#3d5cf5"/><path d="M16 36l10-10 8 6 12-14"/><circle cx="22" cy="54" r="4"/><circle cx="46" cy="54" r="4"/><path d="M34 44v12"/></svg>
    <h3>Executive Training</h3>
    <p>Develop premium positioning strategies that allow you to command higher prices and attract clients who value your expertise.</p>
  </div>
  <div class="abs card svc featured" style="left:460px">
    <svg viewBox="0 0 68 68" fill="none" stroke="#3d5cf5" stroke-width="2"><circle cx="34" cy="34" r="24"/><circle cx="34" cy="34" r="14" stroke="#2a9d8f"/><path d="M34 34l7-7M34 4v6M34 58v6M4 34h6M58 34h6" /></svg>
    <h3>Funnel Optimization</h3>
    <p>Analyze and optimize your entire sales and marketing funnel to increase conversion rates and maximize ROI on every customer acquisition.</p>
  </div>
  <div class="abs card svc" style="left:776px">
    <svg viewBox="0 0 68 68" fill="none" stroke="#2a9d8f" stroke-width="2"><circle cx="34" cy="12" r="6" stroke="#3d5cf5"/><path d="M34 18v12M14 30h40M14 30v10M34 30v10M54 30v10"/><circle cx="14" cy="46" r="5"/><circle cx="34" cy="46" r="5" stroke="#3d5cf5"/><circle cx="54" cy="46" r="5"/><path d="M6 62c2-6 14-6 16 0M26 62c2-6 14-6 16 0M46 62c2-6 14-6 16 0"/></svg>
    <h3>Demand Generation</h3>
    <p>Implement cutting-edge demand generation strategies that attract high-value clients and position your business as the industry leader.</p>
  </div>
  <div class="abs btn" style="left:494px;top:477px;width:226px;height:44px">View More Services
    <svg viewBox="0 0 12 12"><path d="M2 10L10 2M4 2h6v6" stroke="#fff" stroke-width="1.5" fill="none"/></svg>
  </div>
</section>

<section class="section video">
  <h2 class="abs heading center-title" style="top:82px">Discover How We Transform <span class="accent">Marketing Funnels</span></h2>
  <p class="abs center-sub" style="top:152px;width:700px">Discover how we equip business leaders with the frameworks needed to transform their sales.</p>
  <div class="abs frame">
    <div class="screen" role="img" aria-label="Video still of three professionals reviewing a tablet at a conference table">
      <div class="play"><svg width="26" height="28" viewBox="0 0 26 28"><polygon points="4,2 24,14 4,26" fill="#1b1f2a"/></svg></div>
      <div class="bar"><span></span></div>
      <div class="time" style="left:26px">10:55</div>
      <div class="time" style="right:26px">02:10:55</div>
    </div>
  </div>
  <p class="abs center-sub" style="top:744px;width:790px;font-size:12px">Learn how our proven frameworks help high-ticket service businesses attract premium clients and increase conversion rates. But I must explain to you how all this mistaken idea of denouncing pleasure and praising pain was born and I will give you a complete account of the system, and expound the actual teachings of the great explorer of the truth.</p>
  <div class="abs btn" style="left:494px;top:838px;width:212px;height:44px">Watch More Videos
    <svg viewBox="0 0 12 12"><path d="M2 10L10 2M4 2h6v6" stroke="#fff" stroke-width="1.5" fill="none"/></svg>
  </div>
</section>

<section class="section stats">
  <div class="abs stat" style="left:77px"><div class="num">150<b>+</b></div><div class="lbl">Clients Served</div></div>
  <div class="abs divider" style="left:318px"></div>
  <div class="abs stat" style="left:341px"><div class="num">$47<b>M</b></div><div class="lbl">Revenue Generated</div></div>
  <div class="abs divider" style="left:601px"></div>
  <div class="abs stat" style="left:615px"><div class="num">3.2<b>X</b></div><div class="lbl">Avg. ROI Increase</div></div>
  <div class="abs divider" style="left:869px"></div>
  <div class="abs stat" style="left:877px"><div class="num">92<b>%</b></div><div class="lbl">Client Retention</div></div>
</section>

<section class="section about">
  <div class="abs copy">
    <h2 class="heading">About Reach <span class="accent">Crafters</span></h2>
    <div class="lead">Empowering Business Leaders to Master Demand.</div>
    <p class="body">At Reach Crafters, we believe every high-ticket service business deserves access to the same strategic frameworks used by Fortune 500 companies.</p>
    <p class="body">Our team brings together decades of experience in marketing strategy, sales optimization, and business development. We've distilled the best practices from leading business schools and real-world success stories into actionable systems that drive results.</p>
    <p class="body">Transform data into action with our comprehensive analytics dashboards and continuous optimization strategies for maximum ROI.</p>
    <div class="btn">Learn More
      <svg viewBox="0 0 12 12"><path d="M2 10L10 2M4 2h6v6" stroke="#fff" stroke-width="1.5" fill="none"/></svg>
    </div>
  </div>
  <div class="abs badge"><b>30</b><span>Years Of<br>Experience</span></div>
  <div class="abs" style="left:842px;top:87px;width:220px;height:300px;background:linear-gradient(150deg,#dfe3e8,#8f8276 45%,#4a4f5a)" role="img" aria-label="Two smiling consultants holding a tablet in a bright office"></div>
  <div class="abs" style="left:628px;top:232px;width:283px;height:236px;background:linear-gradient(135deg,#e9ecf0,#aeb4bd 50%,#6c7480);border:4px solid #fff" role="img" aria-label="Hands reviewing printed charts and reports on a desk"></div>

  <div class="abs feature" style="left:142px"><h4>Proven Methods</h4><p>Save 20-40% on monthly bills<br>Reduce your monthly expenses.</p></div>
  <div class="abs feature" style="left:383px"><h4>Strategic Focus</h4><p>We only get paid a portion of<br>the savings we find.</p></div>
  <div class="abs feature" style="left:627px"><h4>Results-Driven</h4><p>Our analysts have unique<br>insights into securing best rates.</p></div>
  <div class="abs feature" style="left:871px"><h4>Partnership</h4><p>Continuous monitoring to ensure<br>the lowest possible costs.</p></div>
</section>

<section class="section blog">
  <h2 class="abs heading center-title" style="top:82px">Insights Latest From <span class="accent">Our Blog</span></h2>
  <p class="abs center-sub" style="top:150px;width:760px">Move beyond basic analytics to the intelligence frameworks that drive strategic marketing decisions in Fortune 500 companies.</p>

  <div class="abs arrow off" style="left:69px;top:391px"><svg width="10" height="10" viewBox="0 0 10 10"><path d="M6.5 1.5L3 5l3.5 3.5" stroke="#fff" stroke-width="1.6" fill="none"/></svg></div>
  <div class="abs arrow on" style="left:1105px;top:391px"><svg width="10" height="10" viewBox="0 0 10 10"><path d="M3.5 1.5L7 5 3.5 8.5" stroke="#fff" stroke-width="1.6" fill="none"/></svg></div>

  <article class="abs card post" style="left:142px">
    <div class="img" style="background:linear-gradient(135deg,#eef0f3,#b9bec6 50%,#7b8390)" role="img" aria-label="Business charts and a laptop on a desk"></div>
    <div class="meta"><div class="date">Dec 15, 2024</div><h3>5 Funnel Mistakes High-Ticket Services Make</h3><p>A software company with approximately 700 employees faced inconsistencies in payroll processing and wireless.</p>
    <div class="more">Read More <svg width="18" height="10" viewBox="0 0 18 10"><path d="M0 5h16M12 1l4 4-4 4" stroke="#3d5cf5" stroke-width="1.6" fill="none"/></svg></div></div>
  </article>
  <article class="abs card post" style="left:460px">
    <div class="img" style="background:linear-gradient(135deg,#d8dde2,#6f6a66 45%,#3b3f48)" role="img" aria-label="Two business people shaking hands across a meeting table"></div>
    <div class="meta"><div class="date">Dec 5, 2024</div><h3>Building a Sales Team That Closes High-Ticket Deals</h3><p>A software company with approximately 700 employees faced inconsistencies in payroll processing and wireless.</p>
    <div class="more">Read More <svg width="18" height="10" viewBox="0 0 18 10"><path d="M0 5h16M12 1l4 4-4 4" stroke="#3d5cf5" stroke-width="1.6" fill="none"/></svg></div></div>
  </article>
  <article class="abs card post" style="left:776px">
    <div class="img" style="background:linear-gradient(135deg,#f0f2f5,#c4c9d1 50%,#8d939c)" role="img" aria-label="Hands typing on a laptop with marketing network graphics overlay"></div>
    <div class="meta"><div class="date">Dec 10, 2024</div><h3>The Metrics That Actually Matter for B2B Services</h3><p>A software company with approximately 700 employees faced inconsistencies in payroll processing and wireless.</p>
    <div class="more">Read More <svg width="18" height="10" viewBox="0 0 18 10"><path d="M0 5h16M12 1l4 4-4 4" stroke="#3d5cf5" stroke-width="1.6" fill="none"/></svg></div></div>
  </article>
  <div class="abs dots" style="left:549px;top:647px"><i></i><i></i><i class="on"></i><i></i><i></i></div>
</section>

<section class="section cta-band">
  <h2 class="abs">Ready to Transform Your Demand<br>Generation With Us?</h2>
  <p class="abs">Schedule a free strategy session and discover how our frameworks.</p>
  <div class="abs subscribe"><span>Enter your mail here...</span>
    <b><svg width="18" height="18" viewBox="0 0 18 18"><path d="M16 2L2 8l6 2 2 6z" fill="#fff"/></svg></b>
  </div>
</section>

<section class="section testimonials">
  <h2 class="abs heading center-title" style="top:82px">What Our <span class="accent">Clients Say</span> About Us</h2>
  <p class="abs center-sub" style="top:146px;width:740px">Join hundreds of high-ticket service business leaders who have increased their lead quality, conversion rates, and average deal size with our proven frameworks.</p>

  <div class="abs arrow off" style="left:78px;top:357px"><svg width="10" height="10" viewBox="0 0 10 10"><path d="M6.5 1.5L3 5l3.5 3.5" stroke="#fff" stroke-width="1.6" fill="none"/></svg></div>
  <div class="abs arrow on" style="left:1093px;top:357px"><svg width="10" height="10" viewBox="0 0 10 10"><path d="M3.5 1.5L7 5 3.5 8.5" stroke="#fff" stroke-width="1.6" fill="none"/></svg></div>

  <div class="abs card review" style="left:142px">
    <div class="avatar" role="img" aria-label="Portrait of client"></div>
    <h4>Clara M. Hollis</h4><div class="role">CFO, Northpeak Systems, Inc.</div><div class="stars">★★★★★</div>
    <p>Lorem Ipsum is simply dummy text of the printing and typesetting industry. Lorem Ipsum has been the industry's standard dummy text ever since the</p>
  </div>
  <div class="abs card review" style="left:460px">
    <div class="avatar" role="img" aria-label="Portrait of client"></div>
    <h4>Dana Whitfield</h4><div class="role">CFO, The Ridgeline Group, Inc.</div><div class="stars">★★★★★</div>
    <p>Lorem Ipsum is simply dummy text of the printing and typesetting industry. Lorem Ipsum has been the industry's standard dummy text ever since the</p>
  </div>
  <div class="abs card review" style="left:776px">
    <div class="avatar" role="img" aria-label="Portrait of client"></div>
    <h4>Marcus Ortega</h4><div class="role">CFO, The Ridgeline Group, Inc.</div><div class="stars">★★★★★</div>
    <p>Lorem Ipsum is simply dummy text of the printing and typesetting industry. Lorem Ipsum has been the industry's standard dummy text ever since the</p>
  </div>
  <div class="abs dots" style="left:553px;top:557px"><i></i><i></i><i class="on"></i><i></i><i></i></div>
</section>

<footer class="section footer">
  <svg class="top" width="1200" height="140" viewBox="0 0 1200 140">
    <polygon points="0,0 1200,0 1200,0 0,50" fill="#fff"/>
    <polygon points="70,36 720,6 720,14 80,44" fill="#3d5cf5"/>
    <polygon points="1020,0 1200,0 1200,130 1050,100" fill="#2a3a6a" role="img" aria-label="Office desk with analytics charts"/>
  </svg>
  <div class="abs brand">
    <div class="logo">REACH CRAFTERS</div>
    <p>Lorem ipsum dolor sit amet, consectetur adipiscing elit, sed do</p>
  </div>
  <div class="abs follow">Follow Us: <i></i><i class="fill"></i><i></i></div>

  <div class="abs fcol" style="left:450px;top:240px"><h5>Quick Links</h5><ul><li>About us</li><li>Services</li><li>Insights</li><li>Contact Us</li></ul></div>
  <div class="abs fcol" style="left:628px;top:240px"><h5>Services</h5><ul><li>Executive Training</li><li>Funnel Optimization</li><li>Demand Generation</li></ul></div>
  <div class="abs fcol" style="left:842px;top:240px;width:220px"><h5>Contact Details</h5>
    <div class="contact-row"><span class="ic"><svg width="12" height="14" viewBox="0 0 12 14"><path d="M6 13S1 8 1 5a5 5 0 0110 0c0 3-5 8-5 8z" fill="#fff"/><circle cx="6" cy="5" r="1.8" fill="#26324a"/></svg></span><span>123Lorem Ipsum, is simply dummy text, of the printing.</span></div>
    <div class="contact-row" style="align-items:center"><span class="ic blue"><svg width="13" height="13" viewBox="0 0 14 14"><path d="M3 1l2.5 3-1.5 1.5a8 8 0 004.5 4.5L10 8.5l3 2.5-1.5 2C6 13 1 8 1 2.5z" fill="#fff"/></svg></span><span>Phone: (555) 014 2290</span></div>
    <div class="contact-row" style="align-items:center"><span class="ic"><svg width="14" height="10" viewBox="0 0 14 10"><rect x=".5" y=".5" width="13" height="9" fill="#fff"/><path d="M.5.5L7 6l6.5-5.5" stroke="#26324a" fill="none"/></svg></span><span>hello@reachcrafters.com</span></div>
  </div>
  <div class="abs fline"></div>
  <div class="abs copyright">© 2023 Reach Crafters. All rights reserved. | Privacy Policy | Terms of Service</div>
</footer>

</body>
</html>
```